New, modern business card for growing audiology practice

We need a new business card for our audiology practice. Our logo and website have recently changed (more modern) and we want our business cards to reflect this change.
We conduct hearing tests, perform earwax removals, and fit & dispense hearing aids to our patients. We are a family owned practice in which the owner is the one who works directly with the patient. I have attached logos in various formats to use, as well as two ideas I found on this website; as well as a scanned copy of our current logo. Good luck!

Industry/Entity Type

Business

Contact Information for Business Card

Company name: Tolvera Hearing Center
Provider name: Peter Wolstenby, Au.D. F/NSB
Phone number: (802) 683-5127
Address: 837 W. Lindell Ave. Hollin Falls, VT 05741
email: tolverahearing@postvane.com
website: tolverahearing.com

Colors
000000
aaaaaa
dbdbdb
cacaca
9bcb3c
afd23c
cadf82
b1b1b1

Requirements
Must have
• My card must include information in the "details" section. In the attached images, I found a few that I liked and I would like to model after - "brisky bouncin'" and "Sound Method Center".
• Must be horizontal.
• Must include logos provided. I uploaded them in various file formats and various ways.
• Must match logo font, if possible, if not, please get as close as you can.
Nice to have
• I really like the idea of having a color on one side with just the logo and company name and the contact information and provider name on the other side. I also really like the idea of having the main color dominating on the logo/company side with accent of that same color on the contact side of the card.
Should not have
• Must not be vertical.

```html
<!DOCTYPE html>
<html lang="en">
<head>
<meta charset="utf-8">
<title>Tolvera Hearing Center – Business Card</title>
<link rel="stylesheet" href="https://fonts.googleapis.com/css2?family=Open+Sans:wght@300;400;600&family=Roboto+Condensed:wght@700&display=swap">
<style>
  :root {
    --green: #6cab3a;
    --green-dark: #3f8a25;
    --green-light: #9bcb3c;
    --black: #000000;
    --charcoal: #1c1c1c;
    --grey: #aaaaaa;
    --grey-light: #dbdbdb;
    --white: #ffffff;
    --backdrop: #e9e9e6;
  }
  * { box-sizing: border-box; margin: 0; padding: 0; }
  html, body { width: 1200px; height: 913px; overflow: hidden; }
  body {
    background: var(--backdrop);
    font-family: "Open Sans", Arial, sans-serif;
    position: relative;
  }
  .card {
    position: absolute;
    width: 560px;
    height: 320px;
    border-radius: 4px;
    overflow: hidden;
    box-shadow: 0 10px 24px rgba(0,0,0,.18);
  }
  /* Front side */
  .card--front {
    left: 30px; top: 296px;
    background: linear-gradient(135deg, var(--green-light) 0%, var(--green) 55%, var(--green-dark) 100%);
  }
  .front__brand {
    position: absolute;
    left: 90px; top: 128px;
    display: flex; align-items: center; gap: 18px;
    color: var(--white);
  }
  .front__dot {
    width: 46px; height: 46px; border-radius: 50%;
    background: var(--white);
  }
  .front__name {
    font-weight: 400;
    font-size: 30px;
    line-height: 1.05;
    letter-spacing: 1px;
    text-transform: uppercase;
  }
  .front__name span { display: block; font-size: 22px; letter-spacing: 1.5px; }

  /* Back side */
  .card--back {
    left: 610px; top: 296px;
    background: linear-gradient(160deg, #3a3a3a 0%, var(--charcoal) 40%, var(--black) 100%);
  }
  .back__shapes { position: absolute; inset: 0; }
  .back__company {
    position: absolute; left: 30px; top: 38px;
    color: var(--white);
    font-size: 15px; letter-spacing: 1px;
    text-transform: uppercase;
  }
  .back__person { position: absolute; left: 30px; top: 132px; }
  .back__name {
    font-family: "Roboto Condensed", Arial, sans-serif;
    font-weight: 700; font-size: 20px;
    color: var(--green-light);
  }
  .back__role { color: var(--grey-light); font-size: 12px; margin-top: 2px; }
  .back__contact {
    position: absolute; left: 30px; top: 196px;
    list-style: none;
    color: var(--white); font-size: 12.5px; line-height: 1.35;
  }
  .back__contact li { display: flex; gap: 10px; align-items: flex-start; margin-bottom: 2px; }
  .icon { width: 13px; height: 13px; flex: none; margin-top: 2px; fill: var(--green-light); }
</style>
</head>
<body>

<section class="card card--front" aria-label="Card front">
  <div class="front__brand">
    <div class="front__dot"></div>
    <div class="front__name">Tolvera<span>Hearing Center</span></div>
  </div>
</section>

<section class="card card--back" aria-label="Card back">
  <svg class="back__shapes" viewBox="0 0 560 320" aria-hidden="true">
    <path d="M300 0 C318 150 420 256 560 266 L560 0 Z" fill="var(--green)"/>
    <path d="M302 0 C322 140 425 238 560 244 L560 0 Z" fill="var(--white)"/>
  </svg>

  <div class="back__company">Tolvera Hearing Center</div>

  <div class="back__person">
    <div class="back__name">Peter Wolstenby, Au.D. F/NSB</div>
    <div class="back__role">Owner - Audiologist</div>
  </div>

  <ul class="back__contact">
    <li>
      <svg class="icon" viewBox="0 0 12 12"><path d="M6 0a4 4 0 0 0-4 4c0 3 4 8 4 8s4-5 4-8a4 4 0 0 0-4-4zm0 5.5A1.5 1.5 0 1 1 6 2.5a1.5 1.5 0 0 1 0 3z"/></svg>
      <span>837 W. Lindell Ave.<br>Hollin Falls, VT 05741</span>
    </li>
    <li>
      <svg class="icon" viewBox="0 0 12 12"><path d="M2.5 0.5l2 2.5-1.2 1.3a7 7 0 0 0 4.4 4.4L9 7.5l2.5 2-1 2C5 11.5 0.5 7 0.5 1.5z"/></svg>
      <span>(802) 683-5127</span>
    </li>
    <li>
      <svg class="icon" viewBox="0 0 12 12"><path d="M0 2h12v8H0z M0 2l6 4.5L12 2" stroke="#000" stroke-width=".8"/></svg>
      <span>tolverahearing@postvane.com</span>
    </li>
    <li>
      <svg class="icon" viewBox="0 0 12 12"><circle cx="6" cy="6" r="5.5"/><path d="M0.5 6h11M6 0.5c-3 3-3 8 0 11M6 0.5c3 3 3 8 0 11" stroke="#000" stroke-width=".8" fill="none"/></svg>
      <span>www.tolverahearing.com</span>
    </li>
  </ul>
</section>

</body>
</html>
```